VOMRA Pty Ltd Business Card

Looking for a simple yet eye-catching double-sided business card design using my company logo on one side and contact details on the other.

Target Market(s)

Government

Industry/Entity Type

Communication Systems Engineering

Contact Information for Business Card

VOMRA Pty Ltd

Requirements
Nice to have
• Would be great to have a QR code so details can be scanned into contacts

```html
<!DOCTYPE html>
<html lang="en">
<head>
<meta charset="utf-8">
<title>VOMRA Pty Ltd Business Card</title>
<link rel="stylesheet" href="https://fonts.googleapis.com/css2?family=Montserrat:wght@400;500;700&display=swap">
<style>
  :root {
    --page-bg: #d6d7d8;
    --card-light: #5e676c;
    --card-dark: #2e393f;
    --ink-light: #f2f2f2;
    --ink-muted: #dfe2e4;
    --emboss: #262e33;
    --trace: #aeb4b8;
  }
  * { box-sizing: border-box; margin: 0; padding: 0; }
  html, body { width: 1200px; height: 1200px; overflow: hidden; }
  body {
    background: var(--page-bg);
    font-family: "Montserrat", sans-serif;
    position: relative;
  }
  .card {
    position: absolute;
    left: 150px;
    width: 900px;
    height: 514px;
    border-radius: 28px;
    background: linear-gradient(115deg, var(--card-light) 0%, var(--card-dark) 55%, var(--card-dark) 100%);
    overflow: hidden;
  }
  .card--front { top: 60px; }
  .card--back { top: 620px; }

  .brand {
    position: absolute;
    display: flex;
    align-items: center;
    gap: 18px;
    font-weight: 500;
    letter-spacing: 4px;
  }
  .brand__dot { border-radius: 50%; }
  .card--front .brand {
    left: 50%; top: 50%;
    transform: translate(-50%, -50%);
    color: var(--emboss);
    font-size: 110px;
  }
  .card--front .brand__dot { width: 70px; height: 70px; background: var(--emboss); }
  .card--back .brand {
    right: 70px; top: 56px;
    color: var(--ink-light);
    font-size: 64px;
  }
  .card--back .brand__dot { width: 44px; height: 44px; background: var(--ink-light); }

  .circuit {
    position: absolute;
    background: linear-gradient(135deg, rgba(174,180,184,0.45), rgba(174,180,184,0.12));
    border-radius: 6px;
  }
  .circuit--top { left: 0; top: 0; width: 310px; height: 170px; }
  .circuit--bottom { right: 0; bottom: 0; width: 320px; height: 160px; }

  .contact {
    position: absolute;
    left: 96px;
    top: 205px;
    color: var(--ink-light);
  }
  .contact__name { font-size: 36px; font-weight: 700; }
  .contact__role { font-size: 21px; font-weight: 400; color: var(--ink-muted); margin-top: 6px; }
  .contact__list { list-style: none; margin-top: 34px; }
  .contact__item {
    display: flex; align-items: center; gap: 14px;
    font-size: 21px; line-height: 34px;
  }
  .contact__icon { width: 20px; height: 20px; fill: var(--ink-light); flex: none; }
  .contact__address { font-size: 21px; line-height: 30px; margin-top: 10px; padding-left: 34px; }
</style>
</head>
<body>
  <section class="card card--front" aria-label="Card front">
    <div class="brand"><span class="brand__dot"></span>VOMRA</div>
  </section>

  <section class="card card--back" aria-label="Card back">
    <div class="circuit circuit--top" role="img" aria-label="Decorative circuit-trace pattern"></div>
    <div class="circuit circuit--bottom" role="img" aria-label="Decorative circuit-trace pattern"></div>

    <div class="brand"><span class="brand__dot"></span>VOMRA</div>

    <div class="contact">
      <h1 class="contact__name">Dalton Reeve</h1>
      <p class="contact__role">Founder &amp; Director</p>
      <ul class="contact__list">
        <li class="contact__item">
          <svg class="contact__icon" viewBox="0 0 24 24" aria-hidden="true"><path d="M6.6 10.8a15 15 0 0 0 6.6 6.6l2.2-2.2a1 1 0 0 1 1-.25 11.4 11.4 0 0 0 3.6.57 1 1 0 0 1 1 1V20a1 1 0 0 1-1 1A17 17 0 0 1 3 4a1 1 0 0 1 1-1h3.5a1 1 0 0 1 1 1c0 1.25.2 2.46.57 3.6a1 1 0 0 1-.25 1z"/></svg>
          (405)-555-0142
        </li>
        <li class="contact__item">
          <svg class="contact__icon" viewBox="0 0 24 24" aria-hidden="true"><path d="M2 5h20v14H2z M3.5 6.5 12 12.5l8.5-6" fill="none" stroke="#f2f2f2" stroke-width="0"/><path d="M2 5h20v2l-10 6.5L2 7z M2 9l10 6.5L22 9v10H2z"/></svg>
          admin@vomra.com.au
        </li>
        <li class="contact__item">
          <svg class="contact__icon" viewBox="0 0 24 24" aria-hidden="true"><circle cx="12" cy="12" r="9" fill="none" stroke="#f2f2f2" stroke-width="2"/><path d="M3 12h18M12 3c3 3 3 15 0 18M12 3c-3 3-3 15 0 18" fill="none" stroke="#f2f2f2" stroke-width="1.6"/></svg>
          www.vomra.com.au
        </li>
      </ul>
      <p class="contact__address">27 Larkin Lane Westbrook<br>NSW 2190 Australia</p>
    </div>
  </section>
</body>
</html>
```